A 'new law' boutique Australian law firm that provides specialist employment law and people managem

We value helping clients create results with respect workplaces. What differentiates us is we provide actionable training in understanding and dealing with people and ensure legal compliance fits with this approach. We would like a fresh approach to our training overview documents that we currently use in our current law firm (6 attached). Please use pictures, symbols etc consistent with our non-traditional law approach that captures the approach of each training session.. Attached is the logo and draft letterhead for Birchwell Legal which will launch soon.

Target Market(s)

HR Managers and in-house lawyers (non employment specialists) in mid-large Australian companies that are progressive with a relationship based approach to managing employee behaviours and disputes.

Industry/Entity Type

Human Resource

Font styles to use
Sans Serif

Colors
3176b5
33a6d7

Requirements
Must have
• 1 or 2 page PDF for each of the 6 documents that the wording supplied goes into your design which will be pretty similar as we want consistency with our documents

```html
<!DOCTYPE html>
<html lang="en">
<head>
<meta charset="utf-8">
<title>Contact Officer Training</title>
<link rel="stylesheet" href="https://fonts.googleapis.com/css2?family=Exo+2:wght@700;800&family=Open+Sans:wght@400;600;700&display=swap">
<style>
  :root {
    --brand-blue: #1f76c2;
    --brand-blue-dark: #1565ad;
    --brand-sky: #33a6d7;
    --ink: #222;
    --heading-grey: #6b6b6b;
    --row-grey: #bcbdc0;
    --label-grey: #d1d2d4;
    --wave-grey: #3e4148;
    --paper: #ffffff;
  }
  * { box-sizing: border-box; margin: 0; padding: 0; }
  html, body { width: 896px; height: 1200px; overflow: hidden; background: var(--paper); }
  body { font-family: "Open Sans", Arial, sans-serif; color: var(--ink); position: relative; }

  .hero { position: absolute; left: 0; top: 0; width: 896px; height: 300px; }
  .hero-photo {
    position: absolute; inset: 0;
    background: linear-gradient(100deg, #f3f5f8 0%, #e6ebf1 40%, #cdd6e0 70%, #a8b6c6 100%);
  }
  .hero-title {
    position: absolute; left: 30px; top: 28px; width: 400px; height: 160px;
    background: rgba(255,255,255,0.82);
    padding: 10px 0 0 14px;
    font-family: "Exo 2", Arial, sans-serif; color: var(--brand-blue-dark);
    font-weight: 800; line-height: 0.95;
  }
  .hero-title .kicker { font-size: 38px; display: block; letter-spacing: 0.5px; }
  .hero-title .main { font-size: 72px; display: block; letter-spacing: 1px; }
  .hero-wave { position: absolute; left: 0; top: 190px; width: 896px; height: 120px; }

  .need {
    position: absolute; left: 0; top: 300px; width: 896px; height: 186px;
    background: var(--brand-blue); color: #fff;
  }
  .need h2 {
    position: absolute; left: 34px; top: -44px;
    font-family: "Exo 2", Arial, sans-serif; font-weight: 800; font-size: 27px; color: #fff;
  }
  .need-col { position: absolute; top: 18px; width: 386px; font-size: 12.6px; line-height: 1.32; }
  .need-col p + p { margin-top: 14px; }
  .need-col.left { left: 34px; }
  .need-col.right { left: 448px; }

  .overview-title {
    position: absolute; left: 44px; top: 498px;
    font-family: "Exo 2", Arial, sans-serif; font-weight: 800; font-size: 28px; color: var(--heading-grey);
  }
  .overview {
    position: absolute; left: 35px; top: 535px; width: 826px;
    display: grid; grid-template-columns: 225px 1fr; gap: 2px;
    font-size: 10.8px; line-height: 1.3;
  }
  .overview .topic { background: var(--label-grey); padding: 13px 0 0 27px; }
  .overview .detail { background: var(--row-grey); padding: 0 10px 0 25px; display: flex; align-items: center; }
  .h58 { height: 58px; } .h29 { height: 30px; } .h36 { height: 36px; }

  .outcomes-title {
    position: absolute; left: 44px; top: 990px;
    font-family: "Exo 2", Arial, sans-serif; font-weight: 800; font-size: 29px; color: var(--brand-blue-dark);
  }
  .outcomes-intro { position: absolute; left: 44px; top: 1030px; font-size: 12.4px; font-weight: 700; }
  .outcomes-list { position: absolute; left: 44px; top: 1056px; list-style: none; font-size: 12.6px; line-height: 1.3; }

  .brand {
    position: absolute; left: 603px; top: 1072px; width: 270px;
    display: flex; align-items: center; gap: 10px;
  }
  .brand-dot { width: 22px; height: 22px; border-radius: 50%; background: var(--brand-blue); flex: none; }
  .brand-name { font-family: "Open Sans", Arial, sans-serif; font-weight: 600; font-size: 29px; color: var(--brand-blue); white-space: nowrap; }
</style>
</head>
<body>
  <header class="hero">
    <div class="hero-photo" role="img" aria-label="Photo of colleagues' hands with a pen and papers on a meeting table"></div>
    <h1 class="hero-title"><span class="kicker">CONTACT OFFICER</span><span class="main">TRAINING</span></h1>
    <svg class="hero-wave" viewBox="0 0 896 120" preserveAspectRatio="none">
      <path d="M0 32 C200 10 340 60 520 55 C690 50 800 30 896 0 L896 120 L0 120 Z" fill="#1f76c2"/>
      <path d="M0 32 C200 10 340 60 520 55 C640 52 760 40 896 10 L896 14 C760 46 640 60 520 62 C340 66 200 18 0 40 Z" fill="#3e4148"/>
    </svg>
  </header>

  <section class="need">
    <h2>TRAINING NEED</h2>
    <div class="need-col left">
      <p>Unlawful or inappropriate behavior in the workplace that is left unaddressed can impact on productivity and employee retention. Claims can be costly in terms of time and money as well as the impact on mental health from being involved in uncomfortable adversarial processes.</p>
      <p>Clear policies and procedures explaining the organisation’s workplace behavior expectations and how grievances will be managed are a minimum compliance requirement.</p>
    </div>
    <div class="need-col right">
      <p>The challenge is ensuring that employees understand the directions contained in those policies, what is unlawful and inappropriate behaviour and the options available to address those behaviours if they experience them or engage in them.</p>
      <p>Well trained Contact Officers provide another resource to assist the organisation to provide a safe and respectful workplace.</p>
    </div>
  </section>

  <h2 class="overview-title">OVERVIEW</h2>
  <div class="overview">
    <div class="topic h58">Discrimination</div>
    <div class="detail h58">What is direct and indirect discrimination? What are the prescribed attributes?<br>What are the exceptions to the general rules.<br>Practical examples of behaviour that may be discriminatory.</div>
    <div class="topic h58">Harassment</div>
    <div class="detail h58">What is harassment? Are protected attributes relevant to harassment? What is the difference between harassment and sexual harassment? How does the reasonable person test work in relation to harassment? Practical examples of behaviour that may be harassment or sexual harassment.</div>
    <div class="topic h58">Bullying</div>
    <div class="detail h58">What is bullying. Explore how bullying differs to discrimination or inappropriate behaviour. Performance Management - when it will and will not be bullying. Is all workplace conflict bullying?<br>Practical examples of behaviour that may be bullying.</div>
    <div class="topic h29" style="padding-top:7px">Victimisation and Vilification</div>
    <div class="detail h29">What is victimisation? What is Vilification?</div>
    <div class="topic h58">Adverse Action</div>
    <div class="detail h58">What is adverse action and how does it differ to other unlawful behaviour? What is a workplace right?<br>When is it lawful to terminate employment because of an employee’s absence?<br>How are the protected attributes relevant to adverse action?</div>
    <div class="topic h58">The Contact Officer’s role</div>
    <div class="detail h58">How to perform your role when approached by an employee – the 6 step approach. What not to do.<br>What are the obligations with regard to Confidentiality?</div>
    <div class="topic h58" style="padding-top:22px">Grievance Options</div>
    <div class="detail h58">Explore the options of complaint management - self management, internal informal management, formal internal management. How do they compare and what are the advantages and disadvantages of each approach. Is doing nothing an option? External options – advantages and disadvantages. Who decides which option?</div>
    <div class="topic h36" style="padding-top:10px">Test Learning</div>
    <div class="detail h36">Role play, group discussion</div>
  </div>

  <h2 class="outcomes-title">LEARNING OUTCOMES</h2>
  <p class="outcomes-intro">Training will enable participants to perform their role of Contact Officer and to understand:</p>
  <ol class="outcomes-list">
    <li>1 The role and responsibilities of a Contact Officer</li>
    <li>2 What amounts to unlawful workplace behaviour</li>
    <li>3 What is considered inappropriate behaviour in our workplace</li>
    <li>4 How to apply understanding unlawful/inappropriate behaviour to common scenarios</li>
    <li>5 How to address and resolve grievances early</li>
    <li>6 Options to resolve grievances internally and the Contact Officer role</li>
    <li>7 External options and their pros and cons for resolving grievances</li>
  </ol>

  <div class="brand">
    <span class="brand-dot"></span>
    <span class="brand-name">Birchwell Legal</span>
  </div>
</body>
</html>
```